Business Card Design for K&T Global

K&T Global designs and manufactures ball valves which are used in Oil & Gas drilling and production.

```html
<!DOCTYPE html>
<html lang="en">
<head>
<meta charset="utf-8">
<title>K&amp;T Global — Business Card</title>
<link href="https://fonts.googleapis.com/css2?family=Questrial&family=Libre+Baskerville&display=swap" rel="stylesheet">
<style>
  :root {
    --stage: #1c1c1c;
    --card-light: #b4b4b4;
    --card-mid: #9a9a9a;
    --card-dark: #7d7d7d;
    --ink-light: #ffffff;
    --ink-dark: #3a3a3a;
    --ink-faint: rgba(255,255,255,0.10);
    --map-tone: rgba(255,255,255,0.12);
    --badge-fill: rgba(58,58,58,0.18);
  }
  * { margin: 0; padding: 0; box-sizing: border-box; }
  html, body { width: 1200px; height: 960px; overflow: hidden; background: var(--stage); }
  .canvas { position: relative; width: 1200px; height: 960px; }

  .card {
    position: absolute; left: 257px; width: 674px; height: 410px; overflow: hidden;
    background: linear-gradient(180deg, var(--card-dark) 0%, var(--card-mid) 55%, var(--card-light) 100%);
    font-family: "Questrial", sans-serif;
  }
  .card--front { top: 60px; }
  .card--back { top: 508px; }

  .world-map {
    position: absolute; left: 190px; top: 10px; width: 420px; height: 260px;
    background: radial-gradient(ellipse at center, var(--map-tone) 0%, rgba(255,255,255,0.04) 60%, transparent 75%);
  }
  .brand-watermark {
    position: absolute; right: 24px; bottom: 22px;
    font-family: "Questrial", sans-serif; font-size: 58px; line-height: 1; color: var(--ink-faint);
    white-space: nowrap; transform: rotate(-8deg); transform-origin: right bottom;
  }

  .accent-rule { position: absolute; left: 630px; width: 2px; background: var(--ink-light); }
  .card--front .accent-rule { top: 4px; height: 113px; }
  .card--back .accent-rule { top: 3px; height: 114px; }

  .contact { position: absolute; left: 46px; top: 108px; color: var(--ink-light); }
  .contact__name { font-size: 26px; line-height: 30px; }
  .contact__title { font-size: 18px; line-height: 20px; }
  .contact__lines { margin-top: 24px; font-size: 17px; line-height: 24px; }
  .contact__address { margin-top: 24px; font-size: 17px; line-height: 23px; }

  .website { position: absolute; left: 390px; top: 95px; font-size: 21px; color: var(--ink-dark); }

  .brand { position: absolute; left: 47px; top: 318px; display: flex; align-items: center; gap: 12px; }
  .brand__square { width: 30px; height: 30px; background: var(--ink-dark); }
  .brand__name { font-size: 34px; line-height: 1; color: var(--ink-dark); }

  .cert { position: absolute; left: 530px; top: 232px; width: 100px; text-align: center; color: var(--ink-dark); }
  .cert__badge { display: block; margin: 0 auto; }
  .cert__text { margin-top: 14px; font-family: "Libre Baskerville", serif; font-size: 9px; line-height: 12px; }
</style>
</head>
<body>
<main class="canvas">
  <section class="card card--front">
    <div class="world-map" role="img" aria-label="Faint world map decoration"></div>
    <div class="brand-watermark" aria-hidden="true">K&amp;T Global</div>
    <span class="accent-rule"></span>
    <div class="contact">
      <p class="contact__name">Daniel Whitaker</p>
      <p class="contact__title">operations Manager</p>
      <div class="contact__lines">
        <p>phone: (555) 210-4780</p>
        <p>fax: (555) 210-4781</p>
        <p>e-mail: daniel@ktglobalvalve.com</p>
      </div>
      <div class="contact__address">
        <p>2280 Harbor Bend Road</p>
        <p>Riverton, LA 70599</p>
        <p>P.O. Box 482</p>
        <p>Maple Ridge, LA 70591</p>
      </div>
    </div>
  </section>

  <section class="card card--back">
    <div class="world-map" role="img" aria-label="Faint world map decoration"></div>
    <div class="brand-watermark" aria-hidden="true">K&amp;T Global</div>
    <span class="accent-rule"></span>
    <p class="website">www.ktglobalvalve.com</p>
    <div class="brand">
      <span class="brand__square"></span>
      <span class="brand__name">K&amp;T Global</span>
    </div>
    <div class="cert">
      <svg class="cert__badge" width="64" height="64" viewBox="0 0 64 64" role="img" aria-label="Certification badge placeholder">
        <circle cx="32" cy="32" r="30" fill="var(--badge-fill)" stroke="#3a3a3a" stroke-width="2"/>
      </svg>
      <p class="cert__text">Specification 4-2<br>License 4-2-0560</p>
    </div>
  </section>
</main>
</body>
</html>
```